Venture 482 - Lumora Book Cover

I am looking for a Lumora book cover for my book about "Venture 482".
The Book is Titled:
Venture 482 Ascended
Shaping Outcomes: Paths To Unlocking Cosmic Truths
Author is Dorian Pell
Here is a book description that may help you understand more about it:
Inspired by the genius of Edwin Marlowe, this comprehensive guide delves into the ancient wisdom and cutting-edge science behind the 482 method, a powerful tool for manifesting your desires. Whether you're seeking personal growth, financial success, or spiritual enlightenment, this book provides advanced techniques and methods to transform your dreams into reality.
Any questions please ask.
Thanks
Owen

```html
<!DOCTYPE html>
<html lang="en">
<head>
<meta charset="utf-8">
<title>Venture 482 Ascended — Dorian Pell</title>
<link rel="stylesheet" href="https://fonts.googleapis.com/css2?family=Cinzel:wght@400;500&family=Cormorant+Garamond:wght@500&family=Tinos&display=swap">
<style>
  :root {
    --ink-navy: #1e2b34;
    --ink-slate: #2b3a45;
    --glow-orange: #e0683c;
    --glow-deep: #a5422a;
    --cream: #f6e7dc;
  }
  html, body { margin: 0; padding: 0; overflow: hidden; background: var(--ink-navy); }
  .cover {
    position: relative;
    width: 805px; height: 1200px;
    overflow: hidden;
    background: radial-gradient(ellipse at 50% 45%, var(--ink-slate) 0%, var(--ink-navy) 75%);
    color: var(--cream);
    text-align: center;
  }
  .cover-art {
    position: absolute; left: 35px; top: 0; width: 735px; height: 1200px;
    background:
      radial-gradient(ellipse 12% 40% at 50% 8%, rgba(224,104,60,.75), transparent 70%),
      radial-gradient(ellipse 45% 28% at 50% 28%, rgba(224,104,60,.38), transparent 72%),
      radial-gradient(ellipse 14% 45% at 50% 52%, rgba(30,43,52,.95), transparent 80%),
      radial-gradient(ellipse 20% 50% at 50% 60%, rgba(165,66,42,.45), transparent 75%);
  }
  .author {
    position: absolute; top: 76px; left: 0; right: 0;
    font: 400 50px/1 "Cinzel", serif;
    letter-spacing: 0.42em; padding-left: 0.42em;
    text-transform: uppercase;
  }
  .title { margin: 0; font-weight: 400; }
  .title-word {
    position: absolute; left: 0; right: 0; top: 558px;
    font: 400 122px/1 "Cinzel", serif;
    text-shadow: 0 6px 14px rgba(0,0,0,.45);
  }
  .title-number {
    position: absolute; left: 0; right: 0; top: 597px;
    font: 500 400px/1 "Cormorant Garamond", serif;
    font-variant-numeric: lining-nums;
    letter-spacing: -0.09em; padding-right: 0.09em;
    text-shadow: 0 6px 16px rgba(0,0,0,.4);
  }
  .edition {
    position: absolute; top: 940px; left: 0; right: 0;
    font: 400 70px/1 "Cinzel", serif;
    letter-spacing: 0.36em; padding-left: 0.36em;
    text-shadow: 3px 3px 0 rgba(0,0,0,.7);
  }
  .subtitle-lead {
    position: absolute; top: 1031px; left: 0; right: 0;
    font: 400 34px/1 "Tinos", serif; text-transform: uppercase;
  }
  .subtitle-rest {
    position: absolute; top: 1083px; left: 0; right: 0;
    font: 400 30px/1.2 "Tinos", serif;
  }
</style>
</head>
<body>
  <main class="cover">
    <div class="cover-art" role="img" aria-label="Illustration of a dark human silhouette with glowing energy points, surrounded by orange radiating web-like geometric lines and a vertical beam of light"></div>
    <div class="author">Dorian Pell</div>
    <h1 class="title">
      <span class="title-word">Venture</span>
      <span class="title-number">482</span>
    </h1>
    <div class="edition">ASCENDED</div>
    <div class="subtitle-lead">Shaping Outcomes:</div>
    <div class="subtitle-rest">Paths to unlocking<br>cosmic truths</div>
  </main>
</body>
</html>
```